BOLD & MINIMALIST DESIGN NEEDED

We want a very bold but minimalistic business card design that is impactful and utilizes both sides of the business card. Our current logo is included for your use.

We want bold fonts and good use of negative space. We don't want the logo to overpower the design.

Target Market(s)

Professionals who are building new commercial buildings.

Industry/Entity Type

Construction

Contact Information for Business Card

Name, Title, email, office phone, cell phone, website

Font styles to use
Serif
Sans Serif

Requirements
Must have
• Bold design!

```html
<!DOCTYPE html>
<html lang="en">
<head>
<meta charset="utf-8">
<title>Ridgeline Design + Build — Business Card</title>
<link rel="stylesheet" href="https://fonts.googleapis.com/css2?family=Roboto:wght@400;700;900&display=swap">
<style>
  :root {
    --bg: #ece9e4;
    --card-white: #f7f7f7;
    --card-black: #151515;
    --accent: #8fd14f;
    --ink: #111111;
    --text-light: #f2f2f2;
  }
  * { margin: 0; padding: 0; box-sizing: border-box; }
  html, body { width: 1200px; height: 1027px; overflow: hidden; }
  body {
    background: var(--bg);
    font-family: "Roboto", Arial, sans-serif;
    position: relative;
  }
  .card {
    position: absolute;
    left: 240px;
    width: 720px;
    height: 412px;
    border-radius: 22px;
    overflow: hidden;
    background: var(--card-white);
    box-shadow: 0 10px 30px rgba(0,0,0,0.18);
  }
  .card--front { top: 62px; }
  .card--back { top: 553px; }
  .card__split { position: absolute; inset: 0; }
  .contact {
    position: absolute;
    left: 64px;
    top: 66px;
    color: var(--text-light);
  }
  .contact__name { font-size: 32px; font-weight: 700; letter-spacing: 0.3px; }
  .contact__title { font-size: 19px; font-weight: 400; color: var(--accent); margin-top: 2px; }
  .contact__address { font-size: 18px; line-height: 25px; margin-top: 40px; }
  .contact__list { list-style: none; margin-top: 18px; font-size: 18px; line-height: 29px; }
  .contact__list li { display: flex; align-items: center; gap: 10px; }
  .contact__icon { width: 16px; height: 16px; flex: none; }
  .edge-mark {
    position: absolute;
    left: -22px;
    top: 300px;
    width: 44px;
    height: 44px;
    border-radius: 50%;
    background: var(--accent);
  }
  .brand {
    position: absolute;
    display: flex;
    align-items: center;
    gap: 14px;
    color: var(--ink);
    font-weight: 900;
    text-transform: uppercase;
    white-space: nowrap;
  }
  .brand__square { width: 28px; height: 28px; background: var(--accent); flex: none; }
  .brand__name { font-size: 30px; line-height: 34px; letter-spacing: 1px; }
  .card--front .brand { left: 412px; top: 168px; }
  .card--back .brand { left: 50%; top: 50%; transform: translate(-50%, -50%); }
  .card--back .brand__name { font-size: 40px; line-height: 46px; }
  .card--back .brand__square { width: 36px; height: 36px; }
</style>
</head>
<body>

<section class="card card--front" aria-label="Card front">
  <svg class="card__split" width="720" height="412" viewBox="0 0 720 412" aria-hidden="true">
    <path d="M0 0 H370 C300 120 318 300 430 412 H0 Z" fill="var(--card-black)"/>
    <path d="M382 0 C312 120 330 300 442 412" fill="none" stroke="var(--accent)" stroke-width="4"/>
  </svg>
  <span class="edge-mark" aria-hidden="true"></span>

  <div class="contact">
    <p class="contact__name">Marla Quenby</p>
    <p class="contact__title">Owner</p>
    <p class="contact__address">PO Box 456, Harbor Lane<br>2nd street Westbrook</p>
    <ul class="contact__list">
      <li>
        <svg class="contact__icon" viewBox="0 0 16 16" aria-hidden="true"><rect x="2" y="2" width="12" height="12" fill="none" stroke="var(--accent)" stroke-width="2"/></svg>
        (555) 014-2290
      </li>
      <li>
        <svg class="contact__icon" viewBox="0 0 16 16" aria-hidden="true"><rect x="1" y="3" width="14" height="10" fill="var(--accent)"/><path d="M1 3 L8 9 L15 3" fill="none" stroke="var(--card-black)" stroke-width="1.5"/></svg>
        hello@ridgelinebuild.com
      </li>
      <li>
        <svg class="contact__icon" viewBox="0 0 16 16" aria-hidden="true"><circle cx="8" cy="8" r="7" fill="var(--accent)"/><path d="M1 8 H15 M8 1 V15" stroke="var(--card-black)" stroke-width="1"/></svg>
        www.ridgelinebuild.com
      </li>
    </ul>
  </div>

  <div class="brand">
    <span class="brand__square" aria-hidden="true"></span>
    <span class="brand__name">Ridgeline<br>Design + Build</span>
  </div>
</section>

<section class="card card--back" aria-label="Card back">
  <div class="brand">
    <span class="brand__square" aria-hidden="true"></span>
    <span class="brand__name">Ridgeline<br>Design + Build</span>
  </div>
</section>

</body>
</html>
```